Manuka Honey company needs a Upmarket, Luxury Website!

New Zealand, Taranaki based Manuka Honey company Rimu Vale Honey is looking for a new website, we are looking for an upmarket, luxury, serious website design. We export the highest quality quality Manuka Honey, straight from the Taranaki region.

Main export markets are Asia & Europe, also New Zealand & Australia.

Looking to have a beautiful, upmarket, serious, luxurious & graphical experience with mobile optimization in mind. Like the use of product staging/mockups

You can use copy from other websites to build the site and we will change the copy after the design is finished.

***Please include 'Honey Product' mockups in website.

*Will add illustrator files in coming days***

Feel free to make website functional in Shopify, Wordpress or WIX

Target Market(s)

Asia, Europe (main markets) New Zealand, Australia (Submarkets)

Coding

Coded - Design and coding required

Number of Pages Required

4 page

Requirements
Must have
• Home, Shop, About Us, Contact Us

Homepage to include:

Our Products
Company Video (video under construction)
What is MGO/KPS
Newsletter Opt-in

***(Not in Order)***

Please include 'Honey Product' mockups in website.
*Will add illustrator files in coming days
Nice to have
• FAQ & Partnership Inquiries (hyperlink in footer)

```html
<!DOCTYPE html>
<html lang="en">
<head>
<meta charset="utf-8">
<title>Rimu Vale Honey – Manuka Honey</title>
<link href="https://fonts.googleapis.com/css2?family=Jost:wght@400;500;600&family=Mulish:wght@400;600;700&display=swap" rel="stylesheet">
<style>
:root{
  --ink:#1d1d1d;
  --text:#444;
  --hero-a:#e6d38e;
  --hero-b:#f8f0b8;
  --gold-a:#c8a659;
  --gold-b:#f3e6a4;
  --gold-band-a:#d3b066;
  --gold-band-b:#ecdc96;
  --cream:#f4ead7;
  --card:#fdf8ef;
  --dark-card:#2a2a2a;
  --footer:#000;
  --white:#fff;
}
*{margin:0;padding:0;box-sizing:border-box}
html,body{width:1200px;height:3838px;overflow:hidden}
body{position:relative;background:var(--white);font-family:"Mulish",sans-serif;color:var(--text)}
.abs{position:absolute}
.heading{font-family:"Jost",sans-serif;font-weight:500;letter-spacing:5px;color:var(--ink);text-transform:uppercase}
.btn-gold{position:absolute;border-radius:30px;background:linear-gradient(90deg,var(--gold-a),var(--gold-b));font-family:"Jost",sans-serif;font-weight:600;letter-spacing:2px;font-size:14px;color:#3a2d10;display:flex;align-items:center;justify-content:center;text-transform:uppercase;box-shadow:0 4px 10px rgba(150,120,50,.2)}
.arrow{position:absolute;width:30px;height:50px}
.arrow path{fill:none;stroke:#333;stroke-width:3}

/* hero */
.hero{position:absolute;left:0;top:0;width:1200px;height:711px;background:linear-gradient(100deg,var(--hero-a),var(--hero-b) 70%,#f6eca9)}
.hero-scene{position:absolute;left:250px;top:150px;width:700px;height:500px;background:radial-gradient(ellipse at 60% 30%,rgba(210,190,120,.45),rgba(0,0,0,0) 65%)}
.brand{position:absolute;left:92px;top:28px;display:flex;align-items:center;gap:14px;font-family:"Jost",sans-serif;font-weight:500;font-size:26px;letter-spacing:3px;color:#3b3b3b}
.brand-dot{width:40px;height:40px;border-radius:50%;background:#3b3b3b}
.nav{position:absolute;top:37px;left:582px;display:flex;font-family:"Mulish",sans-serif;font-size:14px;color:#111}
.nav span{position:absolute;white-space:nowrap}
.jars{position:absolute;left:142px;top:194px;width:454px;height:380px;border-radius:18px;background:linear-gradient(100deg,#3a1f12,#b2451f 35%,#5a2b8a 55%,#2c1744)}
.hero-title{position:absolute;left:676px;top:238px;font-family:"Jost",sans-serif;font-weight:600;font-size:84px;line-height:76px;letter-spacing:8px;color:#111}
.hero-tag{position:absolute;left:678px;top:413px;font-family:"Jost",sans-serif;font-size:27px;letter-spacing:3.4px;color:#1a1a1a}
.btn-dark{position:absolute;left:677px;top:472px;width:175px;height:47px;border-radius:26px;background:#1e1e1e;color:var(--gold-b);font-family:"Jost",sans-serif;font-weight:500;letter-spacing:2px;font-size:14px;display:flex;align-items:center;justify-content:center}

/* mgo */
.mgo-title{left:136px;top:826px;font-size:37px}
.para{position:absolute;font-size:14px;line-height:23.5px;color:#454545}
.mgo-visual{position:absolute;left:640px;top:780px;width:450px;height:450px}

/* products */
.products{position:absolute;left:0;top:1294px;width:1200px;height:602px;background:var(--cream)}
.products-title{left:0;width:1200px;text-align:center;top:1344px;font-size:34px}
.card{position:absolute;top:1436px;width:243px;height:390px;background:var(--card);box-shadow:0 3px 10px rgba(0,0,0,.06);text-align:center}
.card .jar{position:absolute;left:47px;top:34px;width:149px;height:168px;border-radius:10px}
.card .name{position:absolute;left:0;width:100%;top:232px;font-family:"Jost",sans-serif;font-weight:500;font-size:21px;color:#1a1a1a}
.card .sub{position:absolute;left:0;width:100%;top:260px;font-size:12px;color:#666}
.card .price{position:absolute;left:0;width:100%;top:286px;font-family:"Jost",sans-serif;font-weight:500;font-size:19px;letter-spacing:2px;color:#1a1a1a}
.card .btn-gold{left:52px;top:325px;width:149px;height:39px;font-size:11px}

/* about */
.video{position:absolute;left:100px;top:1996px;width:499px;height:334px;background:linear-gradient(135deg,#6f6a55,#a9a17e 45%,#d9d8cf 70%,#8a8570);box-shadow:0 8px 20px rgba(0,0,0,.15)}
.video-label{position:absolute;left:0;width:100%;top:148px;text-align:center;font-family:"Jost",sans-serif;font-weight:500;letter-spacing:3px;font-size:17px;color:#fff}
.play{position:absolute;left:0;bottom:0;width:64px;height:49px;background:var(--gold-b);display:flex;align-items:center;justify-content:center}
.about-title{left:662px;top:2004px;font-size:34px}

/* testimonials */
.reviews{position:absolute;left:0;top:2464px;width:1200px;height:510px;background:linear-gradient(100deg,var(--gold-band-a),var(--gold-band-b))}
.reviews-title{left:0;width:1200px;text-align:center;top:2518px;font-size:34px;color:#fff}
.review{position:absolute;top:2644px;width:306px;height:258px;border:1px solid rgba(255,255,255,.75);padding:72px 40px 0 44px}
.review.active{background:var(--dark-card);border-color:var(--dark-card);box-shadow:0 10px 24px rgba(0,0,0,.3)}
.review p{font-size:12.5px;line-height:19px;color:rgba(255,255,255,.82)}
.review .who{margin-top:20px;font-weight:700;font-size:11.5px;letter-spacing:.5px;color:#fff}
.avatar{position:absolute;top:2590px;width:108px;height:108px;border-radius:50%;background:radial-gradient(circle at 50% 40%,#c49a78,#6b4a35 70%,#4a3a2a);box-shadow:0 4px 10px rgba(0,0,0,.2)}
.quote-mark{position:absolute;left:24px;top:36px;font-family:"Jost",sans-serif;font-size:70px;line-height:60px;color:rgba(255,255,255,.15)}
.reviews .arrow path{stroke:#fff}

/* newsletter */
.newsletter-bg{position:absolute;left:430px;top:2980px;width:440px;height:420px;background:radial-gradient(ellipse,rgba(220,215,205,.35),rgba(255,255,255,0) 70%)}
.news-title{left:0;width:1200px;text-align:center;top:3090px;font-size:33px}
.news-sub{position:absolute;left:0;width:1200px;text-align:center;top:3147px;font-size:14px;color:#555}
.news-form{position:absolute;left:304px;top:3196px;width:595px;height:58px;border:1px solid #bdb6a6;border-radius:30px;background:#fff}
.news-form span{position:absolute;left:34px;top:19px;font-size:14px;color:#555}
.news-form .btn-gold{left:408px;top:3px;width:180px;height:50px;font-size:15px;box-shadow:none}

/* footer */
.footer{position:absolute;left:0;top:3402px;width:1200px;height:436px;background:var(--footer);color:#fff}
.foot-brand{position:absolute;left:134px;top:104px;display:flex;align-items:center;gap:10px;font-family:"Jost",sans-serif;font-weight:500;font-size:19px;letter-spacing:1px;color:var(--gold-a)}
.foot-brand i{width:20px;height:20px;border-radius:50%;background:var(--gold-a)}
.foot-col{position:absolute;top:90px}
.foot-col h4{font-family:"Jost",sans-serif;font-weight:500;font-size:15px;letter-spacing:2.5px;margin-bottom:22px}
.foot-col li{list-style:none;font-size:13px;line-height:29.8px;color:#e8e8e8}
.foot-col p{font-size:13px;color:#e8e8e8}
.foot-input{position:absolute;left:860px;top:161px;width:233px;height:34px;background:#fff;color:#666;font-size:10px;letter-spacing:.5px;padding:10px 18px}
.foot-btn{position:absolute;left:860px;top:207px;width:233px;height:38px;background:linear-gradient(90deg,var(--gold-a),var(--gold-b));color:#111;font-size:12px;font-weight:700;letter-spacing:1px;display:flex;align-items:center;justify-content:center}
.copy{position:absolute;left:0;width:1200px;text-align:center;top:388px;font-size:12px;color:#ddd}
</style>
</head>
<body>

<!-- Hero -->
<section class="hero">
  <div class="hero-scene" role="img" aria-label="Faint landscape of a snow-capped mountain behind the hero"></div>
  <div class="brand"><span class="brand-dot"></span>RIMU VALE HONEY</div>
  <nav class="nav">
    <span style="left:0;font-weight:700">HOME</span>
    <span style="left:78px">|</span>
    <span style="left:122px">SHOP</span>
    <span style="left:204px">|</span>
    <span style="left:244px">ABOUT US</span>
    <span style="left:354px">|</span>
    <span style="left:396px">CONTACT US</span>
  </nav>
  <div class="jars" role="img" aria-label="Two premium manuka honey jars, orange and purple labels"></div>
  <h1 class="hero-title">MANUKA<br>HONEY</h1>
  <div class="hero-tag">TASTE NEVER NEVER BEFORE</div>
  <div class="btn-dark">LEARN MORE</div>
  <svg class="arrow" style="left:46px;top:340px" viewBox="0 0 30 50"><path d="M24 4 L6 25 L24 46"/></svg>
  <svg class="arrow" style="left:1118px;top:340px" viewBox="0 0 30 50"><path d="M6 4 L24 25 L6 46"/></svg>
</section>

<!-- What is MGO -->
<h2 class="heading abs mgo-title">What is MGO</h2>
<p class="para" style="left:138px;top:891px;width:445px">Lorem Ipsum is simply dummy text of the printing and typesetting industry. Lorem Ipsum has been the industry's standard dummy text ever since the 1500s, when an unknown printer took a galley of type and scrambled it to make a type specimen book. It has</p>
<p class="para" style="left:138px;top:1008px;width:445px">was popularised in the 1960s with the release of Letraset sheets containing Lorem Ipsum passages, and more recently with desktop publishing software like Aldus PageMaker including version</p>
<div class="btn-gold" style="left:137px;top:1110px;width:187px;height:52px">Learn More</div>

<svg class="mgo-visual" viewBox="0 0 450 450">
  <circle cx="225" cy="216" r="186" fill="none" stroke="#9a9a9a" stroke-width="1.2" stroke-dasharray="10 9"/>
  <circle cx="230" cy="194" r="140" fill="#e3e1dc"/>
  <g>
    <circle cx="60" cy="122" r="38" fill="#fff" stroke="#eee"/>
    <path d="M48 112 h24 M50 112 q-4 8 0 22 h20 q4 -14 0 -22" fill="none" stroke="#e0a520" stroke-width="2.5"/>
    <circle cx="386" cy="110" r="38" fill="#fff" stroke="#eee"/>
    <circle cx="386" cy="110" r="6" fill="none" stroke="#e0a520" stroke-width="2.5"/>
    <g fill="none" stroke="#e0a520" stroke-width="2.5"><circle cx="386" cy="98" r="7"/><circle cx="398" cy="110" r="7"/><circle cx="386" cy="122" r="7"/><circle cx="374" cy="110" r="7"/></g>
    <circle cx="50" cy="305" r="38" fill="#fff" stroke="#eee"/>
    <path d="M38 300 l12 -7 12 7 v14 l-12 7 -12 -7z" fill="none" stroke="#e0a520" stroke-width="2.5"/>
    <circle cx="389" cy="289" r="38" fill="#fff" stroke="#eee"/>
    <path d="M377 284 l12 -7 12 7 v14 l-12 7 -12 -7z" fill="none" stroke="#e0a520" stroke-width="2.5"/>
    <circle cx="228" cy="416" r="38" fill="#fff" stroke="#eee"/>
    <path d="M232 400 q10 14 0 24 q-10 -10 0 -24z" fill="#e0a520"/>
    <path d="M218 416 q5 7 0 12 q-5 -5 0 -12z" fill="#e0a520"/>
  </g>
  <rect x="110" y="74" width="220" height="250" rx="110" fill="url(#photo)" role="img" aria-label="Bowl of honey with a dipper and manuka blossom"/>
  <defs>
    <linearGradient id="photo" x1="0" y1="0" x2="1" y2="1">
      <stop offset="0" stop-color="#c5741e"/><stop offset=".45" stop-color="#8a5a2e"/><stop offset="1" stop-color="#5d6b3c"/>
    </linearGradient>
  </defs>
</svg>

<!-- Products -->
<section class="products"></section>
<h2 class="heading abs products-title">Our Products</h2>
<svg class="arrow" style="left:64px;top:1551px" viewBox="0 0 30 50"><path d="M24 4 L6 25 L24 46"/></svg>
<svg class="arrow" style="left:1136px;top:1558px" viewBox="0 0 30 50"><path d="M6 4 L24 25 L6 46"/></svg>

<article class="card" style="left:100px">
  <div class="jar" role="img" aria-label="Manuka honey jar, white label" style="background:linear-gradient(#1d1d1d 30%,#f4f1ea 30%,#f4f1ea 85%,#1d1d1d 85%)"></div>
  <div class="name">Mounka Honey</div><div class="sub">Lorem Ipsum is simply dummy</div>
  <div class="price">$85.00</div><div class="btn-gold">Learn More</div>
</article>
<article class="card" style="left:353px">
  <div class="jar" role="img" aria-label="Manuka honey jar, orange label" style="background:linear-gradient(#1d1d1d 30%,#b4481f 30%,#b4481f 85%,#1d1d1d 85%)"></div>
  <div class="name">Mounka Honey</div><div class="sub">Lorem Ipsum is simply dummy</div>
  <div class="price">$65.00</div><div class="btn-gold">Learn More</div>
</article>
<article class="card" style="left:606px">
  <div class="jar" role="img" aria-label="Manuka honey jar, black label" style="background:linear-gradient(#1d1d1d 30%,#2e2a26 30%,#2e2a26 85%,#1d1d1d 85%)"></div>
  <div class="name">Mounka Honey</div><div class="sub">Lorem Ipsum is simply dummy</div>
  <div class="price">$33.00</div><div class="btn-gold">Learn More</div>
</article>
<article class="card" style="left:860px">
  <div class="jar" role="img" aria-label="Manuka honey jar, blue label" style="background:linear-gradient(#1d1d1d 30%,#1f3f86 30%,#1f3f86 85%,#1d1d1d 85%)"></div>
  <div class="name">Mounka Honey</div><div class="sub">Lorem Ipsum is simply dummy</div>
  <div class="price">$24.00</div><div class="btn-gold">Learn More</div>
</article>

<!-- About -->
<div class="video" role="img" aria-label="Bee on a white manuka flower, company video still">
  <div class="video-label">PLAY VIDEO</div>
  <div class="play"><svg width="18" height="22" viewBox="0 0 18 22"><path d="M2 1 L17 11 L2 21z" fill="#111"/></svg></div>
</div>
<h2 class="heading abs about-title">About Our Company</h2>
<p class="para" style="left:666px;top:2069px;width:425px">Lorem Ipsum is simply dummy text of the printing and typesetting industry. Lorem Ipsum has been the industry's standard dummy text ever since the 1500s, when an unknown printer took a galley of type and scrambled it to make</p>
<p class="para" style="left:666px;top:2186px;width:425px">was popularised in the 1960s with the release of Letraset sheets containing Lorem Ipsum passages, and more recently</p>
<div class="btn-gold" style="left:666px;top:2270px;width:188px;height:50px">Learn More</div>

<!-- Testimonials -->
<section class="reviews">
  <svg class="arrow" style="left:64px;top:280px" viewBox="0 0 30 50"><path d="M24 4 L6 25 L24 46"/></svg>
  <svg class="arrow" style="left:1118px;top:280px" viewBox="0 0 30 50"><path d="M6 4 L24 25 L6 46"/></svg>
</section>
<h2 class="heading abs reviews-title">What People Says</h2>

<div class="review" style="left:124px"><span class="quote-mark">“</span>
  <p>Augiat in pede Fusce tellus Sed metus augue convallis et vehicula ut pulvinar eu ante Integer orci tellus trisAultricies orci ac feugiat suscipit leo massa sodales velit et scelerisque mi tortor at ipsum Proin orci odio commodo</p>
  <div class="who">ARIA STONE</div></div>
<div class="review active" style="left:456px"><span class="quote-mark">“</span>
  <p>Augiat in pede Fusce tellus Sed metus augue convallis et vehicula ut pulvinar eu ante Integer orci tellus trisAultricies orci ac feugiat suscipit leo massa sodales velit et scelerisque mi tortor at ipsum Proin orci odio commodo</p>
  <div class="who">ARIA STONE</div></div>
<div class="review" style="left:784px"><span class="quote-mark">“</span>
  <p>Augiat in pede Fusce tellus Sed metus augue convallis et vehicula ut pulvinar eu ante Integer orci tellus trisAultricies orci ac feugiat suscipit leo massa sodales velit et scelerisque mi tortor at ipsum Proin orci odio commodo</p>
  <div class="who">ARIA STONE</div></div>
<div class="avatar" style="left:222px" role="img" aria-label="Customer portrait"></div>
<div class="avatar" style="left:555px" role="img" aria-label="Customer portrait"></div>
<div class="avatar" style="left:882px;background:radial-gradient(circle at 50% 40%,#b77a52,#7a4a2a 70%,#d88a3a)" role="img" aria-label="Customer portrait"></div>

<!-- Newsletter -->
<div class="newsletter-bg" role="img" aria-label="Faint line drawing of manuka flowers"></div>
<h2 class="heading abs news-title">Sign Up For Our Newsletter</h2>
<div class="news-sub">Lorem Ipsum is simply dummy text of the printing and typesetting industry.</div>
<div class="news-form"><span>Enter Your Email address</span><div class="btn-gold">Subscribe</div></div>

<!-- Footer -->
<footer class="footer">
  <div class="foot-brand"><i></i>Rimu Vale Honey</div>
  <div class="foot-col" style="left:388px"><h4>NAVIGATION</h4>
    <ul><li>Home</li><li>About Us</li><li>Products</li><li>Videos</li><li>Cotnact Us</li></ul></div>
  <div class="foot-col" style="left:607px"><h4>USEFUL LINKS</h4>
    <ul><li>FAQ</li><li>Partnership Inquiries</li><li>Terms</li><li>Shipping &amp; Return</li><li>Cart</li></ul></div>
  <div class="foot-col" style="left:860px"><h4>NEWSLETTER SIGN UP</h4>
    <p>Sign up here to stay up to date</p></div>
  <div class="foot-input">EMAIL ADDRESS</div>
  <div class="foot-btn">SUBSCRIBE</div>
  <div class="copy">Copyright © 2021 Rimu Vale Honey</div>
</footer>

</body>
</html>
```